tallow-brook.com

We are a small dollar lending company that will revolutionize the industry. We will do this by being completely transparent, fee free, etc and an interest rate that normal people can afford to pay. Over 10X less than our competition. We only allow our members to pay bills " bills paid fast", within 72 hours. Payday loans typically charge from 390%-600% with a terrible payback structure. We charge 36%, period, with a payback structure over 12 months. Our site will be very simple and easy to use but elegant at the same time. We do not want the site to be too busy, less is more and easier. We will have; Home, The Story, Why tallowbrook.com, Are you eligible? Members, Clients. To become a member you have to be referred by a current client of tallowbrook.com. A lot of the busy stuff will be saved for the Members and Clients sections. The feel must be elegant, easy to use and very simple to understand. I am looking for the green, white and black combinations of colors, very similar to my logo that was designed by Fernquillo.

```html
<!DOCTYPE html>
<html lang="en">
<head>
<meta charset="utf-8">
<title>tallow-brook.com — Bills Paid Fast</title>
<link href="https://fonts.googleapis.com/css2?family=Arvo:wght@700&family=Ubuntu:wght@300;400;500;700&display=swap" rel="stylesheet">
<style>
  :root{
    --green:#8abf3f;
    --green-btn:#86bd3c;
    --ink:#222;
    --panel:#efefef;
    --line:#cfcfcf;
    --white:#fff;
    --orange-top:#ffc45a;
    --orange-bot:#f7a33a;
    --sky:#cfd2d2;
    --glow:#d9b27e;
    --sea-top:#7a8ca4;
    --sea-bot:#4f6686;
  }
  *{box-sizing:border-box;margin:0;padding:0}
  html,body{width:1200px;height:1176px;overflow:hidden;background:var(--white)}
  body{position:relative;font-family:"Ubuntu",Arial,sans-serif;color:var(--ink)}

  .hero{position:absolute;left:0;top:0;width:1200px;height:622px;overflow:hidden}
  .hero-photo{position:absolute;inset:0;
    background:linear-gradient(180deg,var(--sky) 0%,var(--glow) 28%,var(--sea-top) 40%,var(--sea-bot) 100%);}

  .site-header{position:absolute;left:0;top:43px;width:1200px;height:78px}
  .brand-box{position:absolute;left:0;top:0;width:246px;height:78px;background:rgba(245,245,242,.82)}
  .nav-box{position:absolute;left:253px;top:0;width:947px;height:78px;background:rgba(245,245,242,.72)}
  .brand{position:absolute;left:34px;top:7px;display:flex;align-items:center;gap:11px;text-decoration:none}
  .brand-mark{width:64px;height:64px;border-radius:6px;background:var(--green)}
  .brand-name{font-size:21px;font-weight:400;color:var(--ink)}
  .main-nav{position:absolute;left:300px;top:28px;display:flex}
  .main-nav a{font-size:15px;font-weight:500;color:var(--ink);text-decoration:none;margin-right:37px}
  .owner-login{position:absolute;left:1076px;top:24px;width:105px;height:31px;background:#050505;color:var(--white);
    font-size:13px;font-weight:500;text-decoration:none;display:flex;align-items:center;justify-content:center}

  .hero-copy{position:absolute;left:103px;top:246px;color:var(--white)}
  .hero-kicker{font-family:"Arvo",Georgia,serif;font-weight:700;font-size:40px;line-height:46px}
  .hero-line{font-weight:300;font-size:49px;line-height:54px;letter-spacing:.5px}
  .hero-line strong{font-weight:700}
  .hero-btn{position:absolute;left:106px;top:414px;width:194px;height:48px;border-radius:4px;
    background:linear-gradient(180deg,var(--orange-top),var(--orange-bot));box-shadow:0 1px 2px rgba(0,0,0,.3);
    color:#3a2a10;font-size:15px;font-weight:500;display:flex;align-items:center;justify-content:center;text-decoration:none}

  .join-card{position:absolute;left:187px;top:680px;width:845px;height:328px;background:var(--panel);
    box-shadow:0 0 4px rgba(0,0,0,.18)}
  .join-title{height:71px;background:var(--white);text-align:center;font-size:32px;font-weight:400;color:#333;line-height:72px}
  .join-divider{position:absolute;left:441px;top:86px;width:1px;height:226px;background:var(--line)}
  .join-or{position:absolute;left:424px;top:183px;width:35px;height:35px;border-radius:50%;border:2px solid #bbb;
    background:var(--panel);font-size:13px;color:#666;display:flex;align-items:center;justify-content:center}
  .join-col{position:absolute;top:142px;width:284px;text-align:center}
  .join-col.left{left:75px}
  .join-col.right{left:506px}
  .join-label{font-family:Arial,Helvetica,sans-serif;font-size:16px;color:#333;margin-bottom:20px}
  .join-input{display:block;width:284px;height:30px;border:1px solid #aaa;background:var(--white);padding:0 10px;
    font-size:13px;color:#333;text-align:left;line-height:28px}
  .join-submit{display:block;margin:18px auto 0;width:169px;height:32px;border-radius:2px;background:var(--green-btn);
    color:var(--white);font-size:12px;letter-spacing:.5px;line-height:32px}

  .site-footer{position:absolute;left:0;top:1061px;width:1200px;height:115px;background:var(--green)}
  .site-footer::before{content:"";position:absolute;left:0;top:5px;width:1200px;height:4px;background:var(--white)}
  .footer-nav{position:absolute;left:26px;top:36px;font-size:15px;color:var(--white)}
  .footer-nav a{color:var(--white);text-decoration:none}
  .copyright{position:absolute;left:26px;top:62px;font-family:Arial,sans-serif;font-size:13px;color:var(--white)}
  .social{position:absolute;left:968px;top:49px;display:flex;gap:10px}
  .social span{width:33px;height:33px;border-radius:5px;background:rgba(255,255,255,.85)}
</style>
</head>
<body>
  <section class="hero">
    <div class="hero-photo" role="img" aria-label="Photo of a woman sitting on a cliff facing the sea at sunset"></div>

    <header class="site-header">
      <div class="brand-box"></div>
      <div class="nav-box"></div>
      <a class="brand" href="#"><span class="brand-mark"></span><span class="brand-name">tallow-brook</span></a>
      <nav class="main-nav">
        <a href="#">Home</a><a href="#">The Story</a><a href="#">Why tallowbrook.com</a><a href="#">Are You Eligible?</a><a href="#">Members</a><a href="#">Clients</a>
      </nav>
      <a class="owner-login" href="#">Owner Login</a>
    </header>

    <div class="hero-copy">
      <h1 class="hero-kicker">Bills Paid Fast</h1>
      <p class="hero-line">Bill payment made</p>
      <p class="hero-line">as <strong>EASY</strong> as never before</p>
    </div>
    <a class="hero-btn" href="#">Become Our Member</a>
  </section>

  <section class="join-card">
    <h2 class="join-title">Become Our Member</h2>
    <div class="join-divider"></div>
    <div class="join-or">Or</div>
    <div class="join-col left">
      <p class="join-label">Already have a Referal ID</p>
      <span class="join-input">Enter Here</span>
      <span class="join-submit">SUBMIT</span>
    </div>
    <div class="join-col right">
      <p class="join-label">Enter Your Membership Number</p>
      <span class="join-input">Enter Here</span>
      <span class="join-submit">SUBMIT</span>
    </div>
  </section>

  <footer class="site-footer">
    <nav class="footer-nav">
      <a href="#">Home</a> | <a href="#">The Story</a> | <a href="#">Why tallowbrook.com</a> | <a href="#">Are You Eligible?</a> | <a href="#">Members</a> | <a href="#">Clients</a>
    </nav>
    <p class="copyright">Copyright (c)2013 by tallow-brook.com</p>
    <div class="social" aria-label="Social links"><span></span><span></span><span></span><span></span><span></span></div>
  </footer>
</body>
</html>
```